Poster design for a film called Harbor Lamps

We are looking for a poster for a short film called Harbor Lamps by Copperfield & Lantern Productions. The film is about a night in the life of 6 20 somethings in the city having a weekly Harbor Lamps and the fun that ensues. We are looking for a minimalist poster that communicates a poker game and a fun night with friends. Some items that appear in the film are poker chips, cards, beer bottles, wine glasses, a record player, a guitar, and a city skyline. Please note that we are looking for something minimalist.

Film name - Harbor Lamps
Production Company - Copperfield & Lantern Productions
Director - Robert Ashdown
Writer - Clara Ashdown
Actors - Margaret Holloway, Clara Ashdown, Owen Patrick Dunmore, Frederick Nolby, Tara Vink, Rebecca Sowden
www.copperfieldandlantern.com

```html
<!DOCTYPE html>
<html lang="en">
<head>
<meta charset="utf-8">
<title>Harbor Lamps — Poster</title>
<link rel="stylesheet" href="https://fonts.googleapis.com/css2?family=Big+Shoulders+Display:wght@500;600&family=Big+Shoulders+Inline+Display:wght@700&family=Arimo:wght@700&display=swap">
<style>
  :root {
    --ink: #000000;
    --panel: #0a0a0a;
    --frame: #ebe7dd;
    --gold: #f2d30c;
  }
  * { margin: 0; padding: 0; box-sizing: border-box; }
  html, body {
    width: 1200px;
    height: 507px;
    overflow: hidden;
    background: var(--ink);
  }
  .poster {
    position: relative;
    width: 1200px;
    height: 507px;
    background: var(--ink);
    color: var(--gold);
    font-family: "Big Shoulders Display", "Oswald", sans-serif;
  }
  .title-frame {
    position: absolute;
    left: 20px;
    top: -10px;
    width: 1158px;
    height: 321px;
    border: 8px solid var(--frame);
    background: var(--panel);
  }
  .title-frame svg {
    position: absolute;
    inset: 0;
    width: 100%;
    height: 100%;
  }
  .film-title {
    font-family: "Big Shoulders Inline Display", "Big Shoulders Display", sans-serif;
    font-weight: 700;
    fill: var(--gold);
  }
  .credits {
    position: absolute;
    left: 0;
    width: 1200px;
    display: flex;
    align-items: center;
    justify-content: space-between;
    white-space: nowrap;
    font-weight: 500;
    font-size: 25px;
    line-height: 1;
    text-transform: uppercase;
  }
  .credits-first { top: 348px; padding: 0 64px 0 44px; }
  .credits-second { top: 402px; padding: 0 22px 0 20px; }
  .credit-group { display: flex; align-items: center; gap: 12px; }
  .credit-label {
    display: inline-flex;
    flex-direction: column;
    font-size: 9px;
    line-height: 1;
    letter-spacing: 0.02em;
    margin-right: 3px;
  }
  .credit-label.inline { flex-direction: row; align-self: flex-end; margin-bottom: 2px; }
  .site {
    position: absolute;
    top: 466px;
    left: 0;
    width: 1200px;
    text-align: center;
    font-family: "Arimo", Arial, sans-serif;
    font-weight: 700;
    font-size: 24px;
    letter-spacing: 0.01em;
  }
</style>
</head>
<body>
  <main class="poster">
    <div class="title-frame">
      <svg viewBox="0 0 1142 305" preserveAspectRatio="none" aria-label="Harbor Lamps">
        <text class="film-title" x="30" y="268" font-size="272" textLength="1078" lengthAdjust="spacingAndGlyphs">HARBOR LAMPS</text>
      </svg>
    </div>

    <div class="credits credits-first">
      <span class="credit-group">Copperfield &amp; Lantern Productions <span class="credit-label inline">presents</span></span>
      <span>“Harbor Lamps”</span>
      <span class="credit-group"><span class="credit-label inline">starring</span> Margaret Holloway</span>
      <span>Clara Ashdown</span>
      <span>Owen Patrick Dunmore</span>
    </div>

    <div class="credits credits-second">
      <span>Frederick Nolby</span>
      <span>Tara Vink</span>
      <span>Rebecca Sowden</span>
      <span class="credit-group"><span class="credit-label"><span>written</span><span>by</span></span>Clara Ashdown</span>
      <span class="credit-group"><span class="credit-label"><span>produced</span><span>by</span></span>Copperfield &amp; Lantern Productions</span>
      <span class="credit-group"><span class="credit-label"><span>directed</span><span>by</span></span>Robert Ashdown</span>
    </div>

    <p class="site">copperfieldandlantern.com</p>
  </main>
</body>
</html>
```